Automotive eCommerce Business looking for a business card design

Looking for a clean and simple business card design. Our company name is "Brindle Auto" and we are a company specializing in the ecommerce sales of automotive parts, specifically for pick up trucks and large SUVs. Our company colours are red, black, and white.

Feel free to use the logo provided or create a new logo that you seem fit. Looking forward to your creative ideas!

Industry/Entity Type

Automotive

Contact Information for Business Card

We were thinking of a possibly two-sided design featuring just the logo and company name on one side, and personal information on the other side. Single sided designs will be considered as well.

Font styles to use
Serif
Sans Serif
Decorative

Colors
ec1f27
ffffff
000000

Requirements
Must have
• Space for employee's name, title, phone number and email address, along with the company address and website somewhere.

```html
<!DOCTYPE html>
<html lang="en">
<head>
<meta charset="utf-8">
<title>Brindle Auto Ltd. — Business Card</title>
<link rel="stylesheet" href="https://fonts.googleapis.com/css2?family=Roboto:wght@400;500&family=Roboto+Condensed:wght@500&display=swap">
<style>
  :root {
    --stage: #262626;
    --brand-red: #a31f24;
    --card-white: #f3f3f3;
    --ink: #4a4a4a;
    --ink-strong: #3c3c3c;
    --white: #ffffff;
  }
  * { margin: 0; padding: 0; box-sizing: border-box; }
  html, body { width: 1200px; height: 960px; overflow: hidden; }
  body {
    position: relative;
    background: var(--stage);
    font-family: "Roboto", Arial, sans-serif;
  }
  .card {
    position: absolute;
    left: 320px;
    width: 600px;
    border-radius: 18px;
  }
  .card-front {
    top: 105px;
    height: 345px;
    background: var(--brand-red);
  }
  .card-back {
    top: 493px;
    height: 342px;
    background: var(--card-white);
  }
  .brand-lockup {
    position: absolute;
    display: flex;
    align-items: center;
    gap: 14px;
    font-family: "Roboto", Arial, sans-serif;
    font-weight: 500;
    text-transform: uppercase;
    white-space: nowrap;
  }
  .brand-mark { display: block; flex: none; }
  .card-front .brand-lockup {
    left: 0; right: 0; top: 160px;
    justify-content: center;
    color: var(--white);
    font-size: 30px;
    letter-spacing: 2px;
  }
  .card-front .brand-mark { width: 26px; height: 26px; background: var(--white); }
  .front-website {
    position: absolute;
    left: 0; right: 0; top: 298px;
    text-align: center;
    color: var(--white);
    font-size: 14px;
    letter-spacing: 5px;
  }
  .card-back .brand-lockup {
    left: 340px; width: 226px; top: 170px;
    justify-content: center;
    color: var(--ink-strong);
    font-size: 19px;
    letter-spacing: 1px;
    gap: 10px;
  }
  .card-back .brand-mark { width: 16px; height: 16px; background: var(--brand-red); }
  .contact-block {
    position: absolute;
    left: 34px; top: 117px;
    color: var(--ink);
  }
  .person-name {
    font-family: "Roboto Condensed", "Arial Narrow", sans-serif;
    font-weight: 500;
    font-size: 21px;
    color: var(--brand-red);
    text-transform: uppercase;
    line-height: 24px;
  }
  .person-title {
    font-size: 14.5px;
    font-weight: 500;
    text-transform: uppercase;
    line-height: 22px;
  }
  .address { margin-top: 11px; font-size: 14px; line-height: 18px; }
  .contact-list { list-style: none; margin-top: 10px; font-size: 14px; }
  .contact-list li { display: flex; align-items: center; height: 19px; gap: 9px; }
  .contact-list svg { width: 14px; height: 14px; fill: var(--brand-red); flex: none; }
</style>
</head>
<body>
  <section class="card card-front" aria-label="Card front">
    <div class="brand-lockup"><span class="brand-mark"></span>Brindle Auto Ltd.</div>
    <p class="front-website">www.brindleauto.com</p>
  </section>

  <section class="card card-back" aria-label="Card back">
    <div class="contact-block">
      <h1 class="person-name">Dana Whitcombe</h1>
      <p class="person-title">CEO/Founder</p>
      <p class="address">412 Harrow Creek Road<br>Fairbanks, Alaska 99701</p>
      <ul class="contact-list">
        <li><svg viewBox="0 0 16 16" aria-hidden="true"><path d="M3 1l3 3-1.6 2.2a9 9 0 0 0 5.4 5.4L12 10l3 3-2 2C7 15 1 9 1 3z"/></svg>907 555 0142</li>
        <li><svg viewBox="0 0 16 16" aria-hidden="true"><path d="M4 0h8a1 1 0 0 1 1 1v14a1 1 0 0 1-1 1H4a1 1 0 0 1-1-1V1a1 1 0 0 1 1-1zm1 2v10h6V2zm3 11a1 1 0 1 0 0 2 1 1 0 0 0 0-2z"/></svg>907 555 0187</li>
        <li><svg viewBox="0 0 16 16" aria-hidden="true"><path d="M4 1h8v4H4zM1 6h14v7h-3v2H4v-2H1zm4 5v3h6v-3z"/></svg>907 555 0163</li>
        <li><svg viewBox="0 0 16 16" aria-hidden="true"><path d="M1 3h14v10H1zm1.5 1.3V5l5.5 4 5.5-4v-.7z"/></svg>dana@brindleauto.com</li>
        <li><svg viewBox="0 0 16 16" aria-hidden="true"><circle cx="8" cy="8" r="7"/></svg>www.brindleauto.com</li>
      </ul>
    </div>
    <div class="brand-lockup"><span class="brand-mark"></span>Brindle Auto Ltd.</div>
  </section>
</body>
</html>
```